Business Card Design

Extremely classy understated design.

Printing in fancy scrip or hand writing.

Conservative color scheme such as black print on beige paper. I am sure you have much better ideas than I would have.

I am involved in a number of different businesses and require a simple elegant business card.

I would like a object on the card, such as, a bald eagle, an antique Halden Crestor, a water fall or a beautiful flower.

My name is: Dwight L. Kessler Not Dwight L. Kessler Investments Investments is my occupation Most of the designs are not acceptable. Very disappointed with results.

Industry/Entity Type

Business

Contact Information for Business Card

Dwight L Kessler
Investments
702 555 0187
mirewoodlk@postvane.net

```html
<!DOCTYPE html>
<html lang="en">
<head>
<meta charset="utf-8">
<title>Dwight L Kessler – Business Card</title>
<link rel="stylesheet" href="https://fonts.googleapis.com/css2?family=Open+Sans:wght@400&family=Pinyon+Script&display=swap">
<style>
  :root {
    --canvas-bg: #f4f4f4;
    --card-black: #050505;
    --card-face: #1a1a1a;
    --card-face-edge: #0b0b0b;
    --band: #070707;
    --gold: #d2a83a;
    --gold-light: #f1d27a;
    --gold-deep: #9a7420;
    --silver: #dcdcdc;
    --silver-soft: #b4b4b4;
    --text-light: #f2f2f2;
  }
  * { box-sizing: border-box; margin: 0; padding: 0; }
  html, body {
    width: 1200px;
    height: 900px;
    overflow: hidden;
    background: var(--canvas-bg);
  }
  .canvas {
    position: relative;
    width: 1200px;
    height: 900px;
  }
  .card {
    position: absolute;
    top: 295px;
    width: 540px;
    height: 310px;
    border-radius: 22px;
    overflow: hidden;
    box-shadow: 0 10px 28px rgba(0,0,0,0.22);
  }

  /* Back side */
  .card--back {
    left: 40px;
    background: var(--card-black);
  }
  .back-lines {
    position: absolute;
    left: 0;
    right: 0;
    top: 94px;
    text-align: center;
    font-family: "Open Sans", sans-serif;
    font-size: 19px;
    line-height: 26px;
    color: var(--text-light);
  }
  .back-lines p:nth-child(2),
  .back-lines p:nth-child(4) { color: #c9c9c9; }

  /* Front side */
  .card--front {
    left: 620px;
    background: radial-gradient(ellipse at 55% 45%, var(--card-face) 0%, var(--card-face-edge) 80%);
  }
  .damask-field {
    position: absolute;
    inset: 0;
    background: radial-gradient(ellipse at 55% 50%, rgba(48,48,48,0.5) 0%, rgba(20,20,20,0) 70%);
  }
  .name-band {
    position: absolute;
    left: 0;
    right: 0;
    top: 103px;
    height: 78px;
    background: var(--band);
    border-top: 1.5px solid var(--gold);
    border-bottom: 1.5px solid var(--gold);
  }
  .ornament {
    position: absolute;
    left: 208px;
    width: 196px;
    height: 60px;
  }
  .ornament--top {
    top: 42px;
    background: radial-gradient(ellipse 50% 70% at 50% 100%, rgba(241,210,122,0.85) 0%, rgba(210,168,58,0.7) 40%, rgba(154,116,32,0.3) 75%, rgba(154,116,32,0) 100%);
  }
  .ornament--bottom {
    top: 183px;
    height: 52px;
    background: radial-gradient(ellipse 50% 75% at 50% 0%, rgba(241,210,122,0.85) 0%, rgba(210,168,58,0.7) 40%, rgba(154,116,32,0.3) 75%, rgba(154,116,32,0) 100%);
  }
  .identity {
    position: absolute;
    left: 0;
    right: 0;
    top: 106px;
    padding-left: 40px;
    text-align: center;
  }
  .identity__name {
    font-family: "Pinyon Script", cursive;
    font-size: 46px;
    line-height: 52px;
    font-weight: 400;
    color: var(--silver);
  }
  .identity__role {
    font-family: "Open Sans", sans-serif;
    font-size: 13px;
    line-height: 16px;
    letter-spacing: 6px;
    color: var(--silver-soft);
    margin-top: -6px;
  }
  .contact {
    position: absolute;
    left: 32px;
    bottom: 32px;
    list-style: none;
    font-family: "Open Sans", sans-serif;
    font-size: 17px;
    line-height: 23px;
    color: var(--text-light);
  }
  .contact__item {
    display: flex;
    align-items: center;
    gap: 9px;
  }
  .contact__icon { width: 18px; height: 18px; flex: none; }
</style>
</head>
<body>
<main class="canvas">
  <section class="card card--back" aria-label="Card back">
    <div class="back-lines">
      <p>Company Name</p>
      <p>Company Name or logo</p>
      <p>Company name</p>
      <p>Company name or logo</p>
    </div>
  </section>

  <section class="card card--front" aria-label="Card front">
    <div class="damask-field" role="img" aria-label="Faint black damask pattern across the card"></div>
    <div class="ornament ornament--top" role="img" aria-label="Gold baroque flourish ornament above the name band"></div>
    <div class="name-band"></div>
    <div class="ornament ornament--bottom" role="img" aria-label="Gold baroque flourish ornament below the name band"></div>
    <div class="identity">
      <h1 class="identity__name">Dwight L Kessler</h1>
      <p class="identity__role">Investments</p>
    </div>
    <ul class="contact">
      <li class="contact__item">
        <svg class="contact__icon" viewBox="0 0 24 24" aria-hidden="true">
          <path fill="#d2a83a" d="M6.6 10.8a15.1 15.1 0 0 0 6.6 6.6l2.2-2.2a1 1 0 0 1 1-.25 11.4 11.4 0 0 0 3.6.57 1 1 0 0 1 1 1V20a1 1 0 0 1-1 1A17 17 0 0 1 3 4a1 1 0 0 1 1-1h3.5a1 1 0 0 1 1 1c0 1.250.2 2.45.57 3.57a1 1 0 0 1-.25 1z"/>
        </svg>
        <span>702 555 0187</span>
      </li>
      <li class="contact__item">
        <svg class="contact__icon" viewBox="0 0 24 24" aria-hidden="true">
          <rect x="2" y="5" width="20" height="14" rx="1.5" fill="#d2a83a"/>
          <path d="M3 6.5l9 6.5 9-6.5" fill="none" stroke="#0b0b0b" stroke-width="1.6"/>
        </svg>
        <span>mirewoodlk@postvane.net</span>
      </li>
    </ul>
  </section>
</main>
</body>
</html>
```